New Business Card Design Project

We require a business card design for Vexalund, a newly established Indian company.
Our focus is on the development, manufacturing, and export of a diverse array of pharmaceutical products on a global scale. The card should convey a professional appearance, as our primary markets are in Africa, China, and Southeast Asian nations.
We envision a two-sided business card, with the reverse side dedicated to a logo set against a solid color or an elegantly designed pattern. The corners should be rounded. We would appreciate seeing both horizontal and vertical design options. We trust the designer to utilize their expertise in creating this design.

The content for the business card is included in the attached Word file.

Target Market(s)

Our primary markets are in Africa, China, and Southeast Asian, Latin America, Maldives, Sri Lanka

Industry/Entity Type

Pharmaceutical Manufacturing and Export

Contact Information for Business Card

Colors

Designer to choose colors to be used in the design.

Requirements
Must have
• The reverse side of the business card features solely the logo along with the tagline, "Wellness for All."
Should not have
• The logo should not exceed two instances, encompassing both the front and back sides of the card.

```html
<!DOCTYPE html>
<html lang="en">
<head>
<meta charset="utf-8">
<title>Vexalund Business Card</title>
<link href="https://fonts.googleapis.com/css2?family=Arimo:wght@400;700&display=swap" rel="stylesheet">
<style>
  :root {
    --backdrop: #3f3f3f;
    --brand-blue: #29a9e1;
    --brand-blue-soft: #5cc4ef;
    --brand-red: #f05a4a;
    --paper: #ffffff;
  }
  * { margin: 0; padding: 0; box-sizing: border-box; }
  html, body {
    width: 1200px; height: 803px; overflow: hidden;
    background: var(--backdrop);
    font-family: "Arimo", Arial, sans-serif;
  }
  .stage {
    position: relative; width: 1200px; height: 803px;
    display: flex; align-items: center; justify-content: center; gap: 60px;
  }
  .card {
    position: relative; width: 540px; height: 310px;
    border-radius: 22px; overflow: hidden;
    background: var(--brand-blue);
  }
  /* Front */
  .front-flap { position: absolute; inset: 0; width: 100%; height: 100%; }
  .front-brand {
    position: absolute; left: 340px; top: 118px;
    display: flex; align-items: center; gap: 10px;
  }
  .brand-dot { width: 16px; height: 16px; border-radius: 50%; background: var(--brand-red); }
  .brand-name {
    font-weight: 700; font-size: 34px; color: var(--brand-blue); letter-spacing: 0.5px;
  }
  .holder { position: absolute; left: 28px; top: 44px; color: var(--paper); }
  .holder-name { font-weight: 700; font-size: 21px; color: var(--brand-red); }
  .holder-role { font-size: 12px; margin-top: 4px; }
  .address {
    position: absolute; left: 28px; top: 170px;
    color: var(--paper); font-size: 12.5px; line-height: 16px;
  }
  .contacts {
    position: absolute; left: 28px; top: 218px;
    list-style: none; color: var(--paper); font-size: 12.5px; line-height: 18px;
  }
  .contacts li { display: flex; align-items: center; gap: 7px; }
  .contacts svg { width: 11px; height: 11px; flex: none; }
  /* Back */
  .back-content {
    position: absolute; inset: 0;
    display: flex; flex-direction: column; align-items: center; justify-content: center; gap: 26px;
  }
  .back-name { font-weight: 700; font-size: 46px; color: var(--brand-blue-soft); letter-spacing: 1px; }
  .tagline { font-size: 14px; color: var(--paper); letter-spacing: 0.4px; }
</style>
</head>
<body>
<main class="stage">
  <section class="card card-front" aria-label="Business card front">
    <svg class="front-flap" viewBox="0 0 540 310" aria-hidden="true">
      <polygon points="372,0 540,0 540,310 464,310 254,189" fill="var(--paper)"/>
      <polyline points="372,-2 254,189 464,312" fill="none" stroke="var(--brand-red)" stroke-width="4"/>
    </svg>
    <div class="front-brand">
      <span class="brand-dot"></span>
      <span class="brand-name">Vexalund</span>
    </div>
    <div class="holder">
      <p class="holder-name">Rohan K. Desai</p>
      <p class="holder-role">CEO</p>
    </div>
    <p class="address">12, Lotus Park, Nashik<br>422001, India</p>
    <ul class="contacts">
      <li>
        <svg viewBox="0 0 12 12"><path d="M2.5 1 L4.5 1 L5 3.5 L3.8 4.4 Q5 7 7.6 8.2 L8.5 7 L11 7.5 L11 9.5 Q10.5 11 9 11 Q1 10 1 3 Q1 1.5 2.5 1 Z" fill="var(--brand-red)"/></svg>
        +919800012345
      </li>
      <li>
        <svg viewBox="0 0 12 12"><rect x="0.5" y="2" width="11" height="8" fill="var(--brand-red)"/><path d="M0.5 2 L6 6.5 L11.5 2" fill="none" stroke="var(--paper)" stroke-width="1"/></svg>
        rdesai@vexalund.com
      </li>
      <li>
        <svg viewBox="0 0 12 12"><circle cx="6" cy="6" r="5.5" fill="var(--brand-red)"/><path d="M0.5 6 H11.5 M6 0.5 Q3 6 6 11.5 M6 0.5 Q9 6 6 11.5" fill="none" stroke="var(--paper)" stroke-width="0.8"/></svg>
        www.vexalund.com
      </li>
    </ul>
  </section>

  <section class="card card-back" aria-label="Business card back">
    <div class="back-content">
      <p class="back-name">Vexalund</p>
      <p class="tagline">Wellness for All</p>
    </div>
  </section>
</main>
</body>
</html>
```